Brand new letterhead, business card, email signature etc.

We are a financial company in London, UK. Our website is www.marlowvane.com. We're wanting a complete remodel of the company colours, letter head, business cards, email signatures, etc. Looking to keep the same font for the company name. I have upload a colour palette that we want to work with. We're looking for company letterhead for outgoing letters/ correspondence, letterhead for internal documentation, email signatures, e-letters. etc. Ultimately we will redesign the entire website also. It is important that our clients get a strong, secure, warm, trustworthy, solid feeling and first impression.
Updates

Designs look the same

Target Market(s)

Institutional investors, (ultra) high net worth individuals

Industry/Entity Type

Finance, Invesments banking.

Font styles to use
Other font styles liked:
• Current font is "Champagne & Limousines"

Requirements
Must have
• Must use the colours provided on the PDF uploaded to the portal. The purple = main colour. The red = accent colour.
Nice to have
• Nice to use same font as now for the company name "Corvane". Font is "Champagne & Limousines". Nice to have some reference to the old logo flower, but only subtle.
Should not have
• Do not use the colour red from our website. Use the colours provided on the colour palette PDF that I uploaded in the portal.

```html
<!DOCTYPE html>
<html lang="en">
<head>
<meta charset="utf-8">
<title>Corvane Stationery</title>
<link href="https://fonts.googleapis.com/css2?family=Josefin+Sans:wght@300&family=Lato:wght@400;700&family=Montserrat:wght@400;700&family=Dancing+Script:wght@500&display=swap" rel="stylesheet">
<style>
:root{
  --plum:#2c0019;
  --accent:#c8321e;
  --paper:#e6e6e6;
  --ink:#2a2a2a;
  --backdrop:#d3d3d3;
  --line-soft:#5a3a4c;
}
*{margin:0;padding:0;box-sizing:border-box}
html,body{width:1200px;height:971px;overflow:hidden;background:var(--backdrop)}
.canvas{position:relative;width:1200px;height:971px;font-family:"Lato",sans-serif;color:var(--ink)}
.piece{position:absolute;overflow:hidden}
.wave{position:absolute;left:0;top:0;width:100%;height:100%}
.brand{position:absolute;display:flex;align-items:center}
.brand-mark{border:1px solid currentColor;flex:none}
.brand-name{font-family:"Josefin Sans",sans-serif;font-weight:300;letter-spacing:.14em;line-height:1}
.icon{display:inline-block;width:.9em;height:.9em;vertical-align:-.1em;margin-right:.35em}

/* letterhead back */
.letter-back{left:49px;top:232px;width:503px;height:646px;background:var(--plum)}
.letter-back .floral{position:absolute;left:40px;top:360px;width:420px;height:280px;background:radial-gradient(ellipse at 50% 60%,rgba(120,80,100,.25),rgba(44,0,25,0) 70%)}

/* letterhead */
.letterhead{left:131px;top:32px;width:505px;height:685px;background:var(--paper)}
.letterhead .brand{left:35px;top:41px;color:#333}
.letterhead .brand-mark{width:49px;height:49px;margin-right:12px}
.letterhead .brand-name{font-size:27px}
.letterhead .sender{position:absolute;left:362px;top:23px;font-size:9.2px;line-height:12.2px;color:#1e1e1e}
.letterhead .sender .contact{font-size:8px;line-height:10.6px;margin-top:4px}
.letter-body{position:absolute;left:34px;top:173px;width:437px;font-size:9.3px;line-height:10.75px;color:#333}
.letter-body p{margin-bottom:10.7px}
.letter-body .date{margin-bottom:12px}
.letter-body .salute{font-weight:700;font-size:11.5px;margin:8px 0 12px}
.letter-body .regards{margin-top:20px}
.signature{font-family:"Dancing Script",cursive;font-size:22px;color:#2a2a2a;margin-top:14px}

/* business card front */
.card-front{left:665px;top:51px;width:243px;height:137px;background:var(--paper);border-radius:10px}
.card-front .brand-mark{position:absolute;left:34px;top:24px;width:72px;height:72px;border:1px solid #333}
.card-front .divider{position:absolute;left:120px;top:22px;width:1px;height:73px;background:var(--accent)}
.card-front .details{position:absolute;left:129px;top:21px;font-size:5.8px;line-height:8.2px;color:#333}
.card-front .name{font-family:"Montserrat",sans-serif;font-weight:700;font-size:8.3px;color:#333;line-height:10px}
.card-front .name span{color:var(--accent)}
.card-front .gap{height:5px}

/* business card back */
.card-back{left:916px;top:51px;width:243px;height:137px;background:var(--plum);border-radius:10px}
.card-back .brand{left:39px;top:49px;color:#ececec}
.card-back .brand-mark{width:40px;height:40px;margin-right:10px}
.card-back .brand-name{font-size:20px}

/* email signature */
.signature-strip{left:667px;top:206px;width:490px;height:115px;background:var(--paper)}
.signature-strip .brand{left:18px;top:25px;color:#444}
.signature-strip .brand-mark{width:29px;height:29px;margin-right:10px}
.signature-strip .brand-name{font-size:16px}
.signature-strip .rule{position:absolute;top:17px;width:1px;height:46px;background:var(--accent)}
.signature-strip .who{position:absolute;right:186px;top:17px;text-align:right;font-family:"Montserrat",sans-serif;font-size:11.7px;line-height:17px;color:#222}
.signature-strip .who .name{font-weight:700;font-size:13.4px}
.signature-strip .who .name span{color:var(--accent)}
.signature-strip .reach{position:absolute;left:331px;top:15px;font-family:"Montserrat",sans-serif;font-size:11.7px;line-height:17.4px;color:#222}

/* compliment slip */
.slip{left:661px;top:349px;width:488px;height:244px;background:var(--paper)}
.slip .brand{left:18px;top:23px;color:#444}
.slip .brand-mark{width:27px;height:27px;margin-right:5px}
.slip .brand-name{font-size:15px}
.slip .sender{position:absolute;left:17px;top:77px;font-size:7.3px;line-height:10.2px;color:#222}
.slip .sender .contact{margin-top:6px}
.slip .url{position:absolute;right:55px;top:210px;font-size:12.5px;color:#f2f2f2;letter-spacing:.02em}

/* envelope */
.envelope{left:662px;top:632px;width:487px;height:243px;background:var(--paper)}
</style>
</head>
<body>
<div class="canvas">

  <section class="piece letter-back" aria-label="Letterhead reverse">
    <div class="floral" role="img" aria-label="Faint floral line decoration"></div>
  </section>

  <section class="piece letterhead" aria-label="Letterhead">
    <svg class="wave" viewBox="0 0 505 685" preserveAspectRatio="none" aria-hidden="true">
      <path d="M0,580 C60,640 130,662 230,652 S420,612 505,650 L505,685 L0,685Z" fill="var(--plum)"/>
      <path d="M60,620 C125,646 190,650 270,640 S430,614 490,624" fill="none" stroke="#e6e6e6" stroke-width="3"/>
      <path d="M58,615 C120,641 185,645 265,635 S425,609 485,619" fill="none" stroke="var(--accent)" stroke-width="3.5"/>
    </svg>
    <div class="brand"><span class="brand-mark"></span><span class="brand-name">CORVANE</span></div>
    <div class="sender">
      Corvane Group Limited<br>4th Floor, 18 Aldric Yard<br>London, EC2M 7QT
      <div class="contact">
        <svg class="icon" viewBox="0 0 10 10"><path d="M2,1 L4,1 L4.6,3 L3.5,4 Q4.5,6 6,6.5 L7,5.4 L9,6 L9,8 Q5,9 2,5.5 Q1,3 2,1Z" fill="#222"/></svg>020-555-0143<br>
        <svg class="icon" viewBox="0 0 10 10"><rect x="1" y="2.5" width="8" height="5.5" fill="#222"/><path d="M1,2.5 L5,5.5 L9,2.5" fill="none" stroke="#e6e6e6" stroke-width=".8"/></svg>info@marlowvane.com
      </div>
    </div>
    <div class="letter-body">
      <p class="date">January-03-2020</p>
      <p>Mr, John Doe<br>President</p>
      <p>Fenwick Trust<br>123 Street Name, Suite# 10<br>City, State, 120023</p>
      <p class="salute">Dear Mr, John</p>
      <p>Lorem ipsum dolor sit amet, consectetur adipisicing elit, sed do eiusmod tempor incididunt ut labore et dolore magna aliqua. Ut enim ad minim veniam, quis nostrud exercitation ullamco laboris nisi ut aliquip ex ea commodo consequat. Duis aute irure dolor in reprehenderit in voluptate velit esse cillum dolore eu fugiat nulla pariatur.</p>
      <p>Lorem ipsum dolor sit amet, consectetur adipisicing elit, sed do eiusmod tempor incididunt ut labore et dolore magna aliqua. Ut enim ad minim veniam, quis nostrud exercitation ullamco laboris nisi ut aliquip ex ea commodo consequat. Duis aute irure dolor in reprehenderit in voluptate velit esse cillum dolore eu fugiat nulla pariatur.</p>
      <p>Lorem ipsum dolor sit amet, consectetur adipisicing elit, sed do eiusmod tempor incididunt ut labore et dolore magna aliqua. Ut enim ad minim veniam, quis nostrud exercitation ullamco laboris nisi ut aliquip ex ea commodo consequat.</p>
      <p>Excepteur sint occaecat cupidatat non proident, sunt in culpa qui officia deserunt mollit anim id laborum. re et dolore magnam aliquam quaerat voluptatem.</p>
      <p class="regards">Regards</p>
      <div class="signature">Daniel Greaves</div>
    </div>
  </section>

  <section class="piece card-front" aria-label="Business card front">
    <svg class="wave" viewBox="0 0 243 137" preserveAspectRatio="none" aria-hidden="true">
      <path d="M0,88 C40,116 100,122 160,116 S225,104 243,120 L243,137 L0,137Z" fill="var(--plum)"/>
      <path d="M30,108 C80,119 150,113 225,105" fill="none" stroke="var(--accent)" stroke-width="1.8"/>
    </svg>
    <span class="brand-mark"></span>
    <span class="divider"></span>
    <div class="details">
      <div class="name"><span>TOBIN</span> HARLOW</div>
      Managing Director
      <div class="gap"></div>
      22 Wexcombe Lane<br>Suite 3B Wexcombe N1 4RT
      <div class="gap"></div>
      <svg class="icon" viewBox="0 0 10 10"><path d="M2,1 L4,1 L4.6,3 L3.5,4 Q4.5,6 6,6.5 L7,5.4 L9,6 L9,8 Q5,9 2,5.5 Q1,3 2,1Z" fill="#222"/></svg>020-555-0178<br>
      <svg class="icon" viewBox="0 0 10 10"><rect x="1" y="2.5" width="8" height="5.5" fill="#222"/><path d="M1,2.5 L5,5.5 L9,2.5" fill="none" stroke="#e6e6e6" stroke-width=".8"/></svg>tobin@marlowvane.com<br>
      <svg class="icon" viewBox="0 0 10 10"><circle cx="5" cy="5" r="4" fill="#222"/></svg>www.marlowvane.com
    </div>
  </section>

  <section class="piece card-back" aria-label="Business card back">
    <div class="brand"><span class="brand-mark"></span><span class="brand-name">CORVANE</span></div>
  </section>

  <section class="piece signature-strip" aria-label="Email signature">
    <svg class="wave" viewBox="0 0 490 115" preserveAspectRatio="none" aria-hidden="true">
      <path d="M0,57 C40,86 90,96 160,93 S380,80 490,101 L490,115 L0,115Z" fill="var(--plum)"/>
      <path d="M55,80 C120,94 250,89 330,82 S430,78 455,87" fill="none" stroke="var(--accent)" stroke-width="2.5"/>
    </svg>
    <div class="brand"><span class="brand-mark"></span><span class="brand-name">CORVANE</span></div>
    <span class="rule" style="left:161px"></span>
    <div class="who">
      <div class="name"><span>TOBIN</span> HARLOW</div>
      Managing Director<br>Suite 3B Wexcombe N1
    </div>
    <span class="rule" style="left:317px"></span>
    <div class="reach">
      <svg class="icon" viewBox="0 0 10 10"><path d="M2,1 L4,1 L4.6,3 L3.5,4 Q4.5,6 6,6.5 L7,5.4 L9,6 L9,8 Q5,9 2,5.5 Q1,3 2,1Z" fill="#222"/></svg>020-555-0178<br>
      <svg class="icon" viewBox="0 0 10 10"><rect x="1" y="2.5" width="8" height="5.5" fill="#222"/><path d="M1,2.5 L5,5.5 L9,2.5" fill="none" stroke="#e6e6e6" stroke-width=".8"/></svg>tobin@marlowvane.com<br>
      <svg class="icon" viewBox="0 0 10 10"><circle cx="5" cy="5" r="4" fill="#222"/></svg>www.marlowvane.com
    </div>
  </section>

  <section class="piece slip" aria-label="Compliment slip">
    <svg class="wave" viewBox="0 0 488 244" preserveAspectRatio="none" aria-hidden="true">
      <path d="M0,148 C50,186 120,206 220,201 S420,184 488,211 L488,244 L0,244Z" fill="var(--plum)"/>
      <path d="M57,184 C120,206 260,196 340,188 S440,181 460,195" fill="none" stroke="var(--accent)" stroke-width="2.5"/>
    </svg>
    <div class="brand"><span class="brand-mark"></span><span class="brand-name">CORVANE</span></div>
    <div class="sender">
      Corvane Group Limited<br>4th Floor, 18 Aldric Yard<br>London EC2M 7QT
      <div class="contact">
        <svg class="icon" viewBox="0 0 10 10"><path d="M2,1 L4,1 L4.6,3 L3.5,4 Q4.5,6 6,6.5 L7,5.4 L9,6 L9,8 Q5,9 2,5.5 Q1,3 2,1Z" fill="#222"/></svg>020-555-0143<br>
        <svg class="icon" viewBox="0 0 10 10"><rect x="1" y="2.5" width="8" height="5.5" fill="#222"/><path d="M1,2.5 L5,5.5 L9,2.5" fill="none" stroke="#e6e6e6" stroke-width=".8"/></svg>info@marlowvane.com
      </div>
    </div>
    <div class="url">www.marlowvane.com</div>
  </section>

  <section class="piece envelope" aria-label="Envelope">
    <svg class="wave" viewBox="0 0 487 243" preserveAspectRatio="none" aria-hidden="true">
      <path d="M12,46 L6,238 M475,46 L481,238" stroke="#cfcfcf" stroke-width="1" fill="none"/>
      <path d="M0,0 H487 C483,30 478,48 455,51 L243,78 L32,51 C12,48 4,30 0,0Z" fill="var(--plum)"/>
    </svg>
  </section>

</div>
</body>
</html>
```